Design a book cover
TItle: Where Would Mercy Stand?
Suggested graphic: Jesus holding a gun
Subtitle: A public defender's views on the death penalty
Author Name: Gordon Maskelyne

```html
<!DOCTYPE html>
<html lang="en">
<head>
<meta charset="utf-8">
<title>Where Would Mercy Stand? — Book Cover</title>
<link rel="stylesheet" href="https://fonts.googleapis.com/css2?family=Bebas+Neue&family=Montserrat:wght@400&family=Playfair+Display:wght@900&display=swap">
<style>
  :root {
    --paper: #f4eddd;
    --ink: #000000;
    --crimson: #b01917;
    --art-fill: #e6dcc6;
  }
  * { margin: 0; padding: 0; box-sizing: border-box; }
  html, body { width: 800px; height: 1200px; overflow: hidden; background: var(--paper); }
  .cover { position: relative; width: 800px; height: 1200px; background: var(--paper); }

  .subtitle-rule {
    position: absolute; left: 216px; top: 150px;
    width: 2px; height: 178px; background: var(--ink);
  }
  .subtitle {
    position: absolute; left: 239px; top: 148px;
    font-family: "Montserrat", sans-serif; font-weight: 400;
    font-size: 30px; line-height: 36.5px; color: var(--ink);
    letter-spacing: 0.5px;
  }

  .cover-art {
    position: absolute; left: 467px; top: 94px;
    width: 158px; height: 319px;
    background: var(--art-fill); border-radius: 70px 70px 40px 40px;
  }

  .title { position: absolute; left: 0; top: 0; width: 800px; height: 1000px; }
  .title text { font-family: "Playfair Display", serif; font-weight: 900; }
  .title .line-dark { fill: var(--ink); }
  .title .line-red { fill: var(--crimson); }

  .author {
    position: absolute; left: 150px; top: 1052px; width: 492px;
    text-align: center;
    font-family: "Bebas Neue", sans-serif; font-size: 52px; line-height: 1;
    letter-spacing: 12px; color: var(--ink);
    text-indent: 12px;
  }
</style>
</head>
<body>
  <main class="cover">
    <div class="subtitle-rule"></div>
    <p class="subtitle">A public<br>defender’s<br>views on<br>the death<br>penalty</p>

    <div class="cover-art" role="img" aria-label="Illustration of a hand pointing a revolver straight at the viewer"></div>

    <svg class="title" width="800" height="1000" viewBox="0 0 800 1000" role="heading" aria-level="1" aria-label="Where Would Mercy Stand?">
      <text class="line-dark" x="196" y="543" font-size="190" textLength="430" lengthAdjust="spacingAndGlyphs">Where</text>
      <text class="line-dark" x="204" y="666" font-size="140" textLength="417" lengthAdjust="spacingAndGlyphs">Would</text>
      <text class="line-red" x="118" y="801" font-size="195" textLength="520" lengthAdjust="spacingAndGlyphs">Mercy</text>
      <text class="line-red" x="176" y="944" font-size="195" textLength="520" lengthAdjust="spacingAndGlyphs">Stand?</text>
    </svg>

    <p class="author">Gordon Maskelyne</p>
  </main>
</body>
</html>
```